Business card for a new cabinet shop company named Veloran Cabinets for high end cabinets

Design a business card, thinking dark rich green with colours to speak of high end luxury ie; cream, gold, black possibly

Mitchell Tarrowby
Director Craftsman
Email: info@veloranjoinery-example.com.au
Instagram : @veloran.cabinets

```html
<!DOCTYPE html>
<html lang="en">
<head>
<meta charset="utf-8">
<title>Veloran Cabinets – Business Card</title>
<link href="https://fonts.googleapis.com/css2?family=Jost:wght@400;700&display=swap" rel="stylesheet">
<style>
  :root {
    --backdrop: #1f2421;
    --card-green: #0f2a1f;
    --card-green-light: #173a2b;
    --card-green-deep: #0a1f16;
    --gold: #c6a562;
    --ivory: #f4f1ea;
    --cream: #e6dfcf;
  }
  html, body {
    margin: 0;
    padding: 0;
    width: 1200px;
    height: 694px;
    overflow: hidden;
    background: var(--backdrop);
    font-family: "Jost", "Futura", sans-serif;
  }
  .canvas {
    position: relative;
    width: 1200px;
    height: 694px;
  }
  .card {
    position: absolute;
    top: 192px;
    width: 540px;
    height: 310px;
    border-radius: 16px;
    background: var(--card-green);
    box-shadow: 0 18px 40px rgba(0,0,0,0.5);
    overflow: hidden;
  }
  .card--front { left: 40px; }
  .card--back  { left: 620px; }

  /* Front */
  .front-texture {
    position: absolute;
    inset: 0;
    background: radial-gradient(ellipse at 30% 70%, var(--card-green-light) 0%, var(--card-green) 55%, var(--card-green-deep) 100%);
  }
  .front-wordmark {
    position: absolute;
    inset: 0;
    display: flex;
    align-items: center;
    justify-content: center;
    gap: 16px;
  }
  .wordmark-square {
    width: 22px;
    height: 22px;
    background: var(--gold);
    flex: none;
  }
  .wordmark-name {
    font-size: 46px;
    font-weight: 400;
    color: var(--gold);
    letter-spacing: 0.01em;
    line-height: 1;
    white-space: nowrap;
  }

  /* Back */
  .back-layout {
    position: absolute;
    inset: 0 0 10px 0;
    display: flex;
    align-items: center;
    padding: 0 26px 0 28px;
  }
  .back-wordmark {
    display: flex;
    align-items: center;
    gap: 9px;
    width: 196px;
    flex: none;
  }
  .back-wordmark .wordmark-square { width: 13px; height: 13px; }
  .back-wordmark .wordmark-name { font-size: 21px; }
  .divider {
    width: 1.5px;
    height: 170px;
    background: var(--gold);
    margin: 0 22px 0 6px;
    flex: none;
  }
  .contact-block { flex: 1; }
  .person-name {
    margin: 0;
    font-size: 24px;
    font-weight: 700;
    color: var(--gold);
    line-height: 1.1;
    white-space: nowrap;
  }
  .person-role {
    margin: 2px 0 18px;
    font-size: 14px;
    font-weight: 400;
    color: var(--ivory);
  }
  .contact-list {
    list-style: none;
    margin: 0;
    padding: 0;
  }
  .contact-item {
    display: flex;
    align-items: center;
    gap: 8px;
    font-size: 12.5px;
    color: var(--cream);
    margin-bottom: 7px;
    white-space: nowrap;
  }
  .contact-icon {
    width: 13px;
    height: 13px;
    flex: none;
  }
  .gold-edge {
    position: absolute;
    left: 0;
    right: 0;
    bottom: 0;
    height: 6px;
    background: var(--gold);
  }
</style>
</head>
<body>
<main class="canvas">

  <section class="card card--front" aria-label="Card front">
    <div class="front-texture" role="img" aria-label="Subtle embossed repeating brand pattern across the card face"></div>
    <div class="front-wordmark">
      <span class="wordmark-square"></span>
      <span class="wordmark-name">Veloran Cabinets</span>
    </div>
  </section>

  <section class="card card--back" aria-label="Card back">
    <div class="back-layout">
      <div class="back-wordmark">
        <span class="wordmark-square"></span>
        <span class="wordmark-name">Veloran Cabinets</span>
      </div>
      <div class="divider"></div>
      <div class="contact-block">
        <h1 class="person-name">Mitchell Tarrowby</h1>
        <p class="person-role">Director Craftsman</p>
        <ul class="contact-list">
          <li class="contact-item">
            <svg class="contact-icon" viewBox="0 0 14 14" aria-hidden="true">
              <rect x="1" y="3" width="12" height="8" fill="none" stroke="#c6a562" stroke-width="1.4"/>
              <path d="M1 3 L7 8 L13 3" fill="none" stroke="#c6a562" stroke-width="1.4"/>
            </svg>
            info@veloranjoinery-example.com.au
          </li>
          <li class="contact-item">
            <svg class="contact-icon" viewBox="0 0 14 14" aria-hidden="true">
              <circle cx="7" cy="7" r="5.8" fill="none" stroke="#c6a562" stroke-width="1.3"/>
            </svg>
            @veloran.cabinets
          </li>
        </ul>
      </div>
    </div>
    <div class="gold-edge"></div>
  </section>

</main>
</body>
</html>
```